Harbourline Electrical Solutions

On one side. LOGO (underneath:) Commercial Industrial Residential

- NAME & CONTACT DETAILS

Marcus T. Hollings
Project Manager

(Cell icon) (441) 555-0187
(Email icon) hlelectricalsolutions@mailvento.com
(Facebook & Instagram icons )@hlelectricalsolutions

Other side: LOGO - underneath ELECTRICAL CONSTRUCTION & MAINTENANCE . LED LIGHTING & AUTOMATION . LIFE SAFETY SYSTEMS (FIRE ALARM / SECURITY) . DATA & COMMUNICATION

```html
<!DOCTYPE html>
<html lang="en">
<head>
<meta charset="utf-8">
<title>Harbourline Electrical Solutions – Business Card</title>
<link rel="stylesheet" href="https://fonts.googleapis.com/css2?family=Montserrat:wght@500;700&family=Roboto:wght@400&family=Saira+Semi+Condensed:ital,wght@0,700&display=swap">
<style>
  :root{
    --bg:#3b3b3d;
    --card:#ffffff;
    --brand:#0d5a76;
    --ink:#3d3d3f;
    --accent-grey:#4a4a4c;
    --on-brand:#ffffff;
  }
  *{box-sizing:border-box;margin:0;padding:0}
  html,body{width:799px;height:1200px;overflow:hidden;background:var(--bg)}
  .card{position:absolute;left:60px;width:680px;height:389px;background:var(--card);overflow:hidden;box-shadow:0 8px 22px rgba(0,0,0,.35)}
  .card--services{top:130px}
  .card--contact{top:680px}

  /* Services side */
  .wordmark{font-family:"Montserrat",sans-serif;font-weight:700;color:var(--brand);text-transform:uppercase;letter-spacing:.08em;line-height:1.1}
  .card--services .wordmark{position:absolute;top:40px;left:0;right:0;text-align:center;font-size:30px}
  .sectors{font-family:"Montserrat",sans-serif;font-weight:500;color:var(--brand);text-transform:uppercase;letter-spacing:.12em}
  .card--services .sectors{position:absolute;top:100px;left:0;right:0;text-align:center;font-size:15px}
  .service-band{position:absolute;top:150px;left:0;right:0;height:165px;background:var(--brand);display:flex;flex-direction:column;justify-content:center;align-items:center;gap:10px}
  .service-band p{font-family:"Roboto",sans-serif;color:var(--on-brand);font-size:17px;letter-spacing:.01em}
  .social-row{position:absolute;top:336px;left:0;right:0;display:flex;justify-content:center;align-items:center;gap:8px;font-family:"Roboto",sans-serif;font-size:17px;color:var(--ink)}
  .social-dot{width:18px;height:18px;border-radius:50%;background:var(--brand)}
  .social-row .handle{margin-left:6px}

  /* Contact side */
  .contact-panel{position:absolute;inset:0}
  .card--contact .brand-block{position:absolute;left:26px;top:95px;width:240px}
  .card--contact .wordmark{font-size:26px;letter-spacing:.06em}
  .card--contact .sectors{margin-top:14px;font-size:10px;letter-spacing:.08em;color:var(--ink)}
  .person{position:absolute;left:340px;top:90px;color:var(--on-brand)}
  .person__name{font-family:"Saira Semi Condensed",sans-serif;font-weight:700;font-size:27px;letter-spacing:.01em}
  .person__role{font-family:"Roboto",sans-serif;font-size:16px;margin-top:2px}
  .contact-list{position:absolute;left:340px;top:185px;list-style:none;color:var(--on-brand);font-family:"Roboto",sans-serif;font-size:16px}
  .contact-list li{display:flex;align-items:center;gap:10px;height:25px}
  .contact-list svg{width:15px;height:15px;flex:none}
  .contact-list .social-dot{width:14px;height:14px;background:var(--on-brand);flex:none;margin-right:1px}
</style>
</head>
<body>

<section class="card card--services">
  <div class="wordmark">Harbourline Electrical Solutions</div>
  <div class="sectors">Commercial &nbsp;|&nbsp; Industrial &nbsp;|&nbsp; Residential</div>
  <div class="service-band">
    <p>Electrical Construction &amp; Maintenance &nbsp;|&nbsp; Led Lighting &amp; Automation</p>
    <p>Life Safety Systems (Fire Alarm/Security) &nbsp;|&nbsp; Data &amp; Communication</p>
  </div>
  <div class="social-row">
    <span class="social-dot"></span>
    <span class="social-dot"></span>
    <span class="handle">@hlelectricalsolutions</span>
  </div>
</section>

<section class="card card--contact">
  <svg class="contact-panel" viewBox="0 0 680 389" width="680" height="389" aria-hidden="true">
    <path d="M292,0 C258,130 245,280 150,389 L680,389 L680,0 Z" fill="var(--accent-grey)"/>
    <path d="M302,0 C268,130 255,280 164,389 L680,389 L680,0 Z" fill="var(--brand)"/>
  </svg>
  <div class="brand-block">
    <div class="wordmark">Harbourline<br>Electrical<br>Solutions</div>
    <div class="sectors">Commercial | Industrial | Residential</div>
  </div>
  <div class="person">
    <div class="person__name">Marcus T. Hollings</div>
    <div class="person__role">Project Manager</div>
  </div>
  <ul class="contact-list">
    <li>
      <svg viewBox="0 0 24 24"><path fill="#fff" d="M6.6 10.8a15.1 15.1 0 0 0 6.6 6.6l2.2-2.2c.3-.3.7-.4 1-.2 1.1.4 2.3.6 3.6.6.6 0 1 .4 1 1V20c0 .6-.4 1-1 1A17 17 0 0 1 3 4c0-.6.4-1 1-1h3.5c.6 0 1 .4 1 1 0 1.3.2 2.5.6 3.6.1.3 0 .7-.2 1z"/></svg>
      (441) 555-0187
    </li>
    <li>
      <svg viewBox="0 0 24 24"><rect x="2" y="5" width="20" height="14" rx="1.5" fill="#fff"/><path d="M3 6l9 7 9-7" fill="none" stroke="var(--brand)" stroke-width="1.8"/></svg>
      hlelectricalsolutions@mailvento.com
    </li>
    <li><span class="social-dot"></span>@hlelectricalsolutions</li>
    <li><span class="social-dot"></span>@hlelectricalsolutions</li>
  </ul>
</section>

</body>
</html>
```